Navoro & Omvar Automotive Repair Shop. Need a new website design.

We specialize in Navoro & Omvar auto repair, but also work on other Asian import vehicles. We have been in business for 7 years and pride ourselves on high quality auto repair that is fixed right the first time. Would like the automotive repair website to incorporate the colors black, red and white if possible and have our logo and some Navoro and Omvar vehicles included in the website.

Target Market(s)

Navoro & Omvar vehicle owners

Industry/Entity Type

Automotive Repair

Coding

Coded - Design and coding required

Number of Pages Required

5+ page

Colors
EB3D1F
EC4F4E
F09395
F8D3D4
FCEDEE

Requirements
Must have
• Home, Services, Contact Us, Schedule appointment, and a gallery tab that I can add shop pictures to when completed.
Nice to have
• Would like to see example pictures of job next to each service listed.
Should not have
• Service not related to auto repair. Ex. auto detailing, towing, car wash

```html
<!DOCTYPE html>
<html lang="en">
<head>
<meta charset="utf-8">
<title>Contact Us – Corvan Automotive</title>
<link rel="stylesheet" href="https://fonts.googleapis.com/css2?family=Fira+Sans+Extra+Condensed:ital,wght@0,500;0,600;0,700;1,500&family=Open+Sans:ital,wght@0,400;0,600;0,700;1,400&display=swap">
<style>
:root{
  --red:#ee0000;
  --red-dark:#b80000;
  --black:#000;
  --ink:#111;
  --footer:#151515;
  --white:#fff;
  --grey:#f5f5f5;
  --muted:#9a9a9a;
  --line:#e3e3e3;
}
*{box-sizing:border-box;margin:0;padding:0}
html,body{width:766px;height:1200px;overflow:hidden}
body{position:relative;background:var(--white);font-family:"Open Sans",sans-serif;color:var(--ink)}
.abs{position:absolute}
.cond{font-family:"Fira Sans Extra Condensed",sans-serif}

/* header */
.site-header{left:0;top:0;width:766px;height:78px;background:var(--black)}
.brand{left:76px;top:26px;display:flex;align-items:center;gap:6px;color:var(--white);font-weight:700;font-size:12px;letter-spacing:.5px;line-height:1.15;width:130px}
.brand-mark{width:12px;height:12px;background:var(--red);flex:none}
.header-rule{left:0;top:76px;width:222px;height:2px;background:var(--red)}
.top-info{top:13px;display:flex;align-items:center;gap:5px;color:var(--white);font-style:italic;font-size:8.5px;line-height:1.2}
.top-info .ico{width:22px;height:22px;border-radius:50%;background:#cfcfcf;display:flex;align-items:center;justify-content:center;flex:none}
.top-info em{color:var(--red);font-weight:700;font-style:italic}
.stars{color:var(--red);font-size:10px;letter-spacing:-1px;font-style:normal}
.main-nav{top:61px;left:372px;display:flex;gap:21px;font-size:7px;font-weight:700;color:var(--white)}
.main-nav .current{color:var(--red)}

/* hero */
.hero{left:0;top:78px;width:766px;height:201px;background:linear-gradient(100deg,#3a2a2a 0%,#2b2b2d 45%,#5a5a5e 70%,#202022 100%)}
.hero-tint{left:0;top:78px;width:766px;height:201px}
.hero-eyebrow{left:72px;top:145px;display:flex;align-items:center;gap:8px;color:var(--white);font-size:7px;letter-spacing:.6px}
.hero-eyebrow i{display:block;width:26px;height:1px;background:var(--white)}
.hero-title{left:71px;top:158px;color:var(--white);font-size:32px;font-weight:700;line-height:38px;white-space:nowrap}
.hero-text{left:71px;top:198px;width:210px;color:var(--white);font-size:7.2px;line-height:10.5px}

/* touch */
.touch-title{left:0;top:343px;width:766px;text-align:center;font-size:24px;font-weight:700}
.touch-sub{left:0;top:374px;width:766px;text-align:center;font-size:13.5px;font-style:italic;font-weight:500;line-height:14.5px}
.touch-sub a{color:var(--red)}
.info-card{top:432px;width:151px;height:111px;background:var(--white);box-shadow:0 1px 3px rgba(0,0,0,.18);text-align:center}
.info-card.dark{background:var(--black);color:var(--white);clip-path:polygon(27px 0,100% 0,100% 100%,0 100%,0 33px);box-shadow:none}
.info-card .circle{width:29px;height:29px;border-radius:50%;border:1px solid var(--red);margin:20px auto 0;display:flex;align-items:center;justify-content:center}
.info-card.dark .circle{border-color:var(--white)}
.info-card h3{font-size:10px;font-weight:700;margin-top:9px}
.info-card p{font-size:7.2px;line-height:9.5px;margin-top:4px}

/* form */
.grey-band{left:0;top:792px;width:766px;height:153px;background:var(--grey)}
.form-panel{left:72px;top:587px;width:352px;height:305px;background:var(--red);color:var(--white)}
.form-eyebrow{left:95px;top:613px;display:flex;align-items:center;gap:7px;font-size:7px;letter-spacing:.5px;color:var(--white);font-weight:600}
.form-eyebrow i{display:block;width:25px;height:1px;background:var(--white)}
.form-title{left:94px;top:621px;color:var(--white);font-size:24px;font-weight:700}
.form-text{left:95px;top:654px;width:220px;color:var(--white);font-size:7.2px;line-height:11.5px}
.field{background:var(--white);display:flex;align-items:center;justify-content:space-between;padding:0 9px 0 10px;font-size:7px;font-style:italic;color:var(--muted)}
.field.filled{color:var(--ink);font-weight:600}
.field .fi{width:13px;height:13px;border-radius:50%;border:1px solid #777;display:flex;align-items:center;justify-content:center}
.field.area{align-items:flex-start;padding-top:8px}
.submit{left:95px;top:834px;width:118px;height:28px;background:var(--black);color:var(--white);clip-path:polygon(14px 0,100% 0,100% 100%,0 100%,0 14px);display:flex;align-items:center;justify-content:center;gap:5px;font-size:8.5px;font-weight:600;letter-spacing:.4px}
.map-box{left:451px;top:587px;width:246px;height:304px;background:var(--white);box-shadow:0 1px 3px rgba(0,0,0,.25);padding:3px}
.map-fill{width:100%;height:100%;background:linear-gradient(135deg,#eef0f2 0%,#e6ebe8 50%,#dbe8ef 100%)}

/* footer */
.site-footer{left:0;top:945px;width:766px;height:255px;background:var(--footer)}
.footer-brand{left:74px;top:1020px;display:flex;align-items:center;gap:7px;color:var(--white);font-size:15px;font-weight:700;line-height:1.1;width:130px}
.badge{background:#e9e9e9}
.footer-head{top:983px;color:var(--red);font-size:13px;font-weight:700}
.quick-links{left:235px;top:1010px;list-style:none;color:#e8e8e8;font-size:7.3px;line-height:20.4px}
.contact-row{left:324px;display:flex;align-items:center;gap:9px;color:#e8e8e8;font-size:7.3px;line-height:10.5px}
.contact-row .ci{width:19px;height:19px;border-radius:50%;background:#d5d5d5;display:flex;align-items:center;justify-content:center;flex:none}
.contact-row b{color:var(--red);font-weight:600}
.footer-map{left:507px;top:985px;width:188px;height:133px;background:linear-gradient(135deg,#e9edef,#dfe7ea 60%,#d6e3e9);clip-path:polygon(32px 0,100% 0,100% 100%,0 100%,0 33px);border:1px solid #fff}
.social{top:1175px;width:18px;height:18px;border-radius:50%;background:#6a6a6a;border:1px solid #9a9a9a}
.copyright{right:69px;top:1181px;color:var(--white);font-size:7.4px}
</style>
</head>
<body>

<!-- header -->
<header class="abs site-header"></header>
<div class="abs brand"><span class="brand-mark"></span><span>CORVAN AUTOMOTIVE</span></div>
<div class="abs header-rule"></div>
<svg class="abs" style="left:210px;top:50px" width="30" height="28" viewBox="0 0 30 28"><polygon points="12,26 26,2 30,2 16,26" fill="#ee0000"/><polygon points="17,28 30,6 30,10 20,28" fill="#777"/></svg>

<div class="abs top-info" style="left:332px">
  <span class="ico"><svg width="12" height="12" viewBox="0 0 12 12"><circle cx="6" cy="5" r="3.2" fill="none" stroke="#333" stroke-width="1.2"/><path d="M4 8 L3.5 11.5 L6 10 L8.5 11.5 L8 8" fill="#333"/></svg></span>
  <span><span class="stars">★★★★★</span><br>5 Star Service</span>
</div>
<div class="abs top-info" style="left:458px">
  <span class="ico"><svg width="12" height="12" viewBox="0 0 12 12"><path d="M2 2 L10 10 M10 2 L2 10" stroke="#333" stroke-width="1.6" stroke-linecap="round"/></svg></span>
  <span>Quality Service<br><em>Guarantee</em></span>
</div>
<div class="abs top-info" style="left:590px">
  <span class="ico"><svg width="12" height="12" viewBox="0 0 24 24"><path d="M6.6 10.8a15 15 0 0 0 6.6 6.6l2.2-2.2c.3-.3.7-.4 1-.2 1.1.4 2.3.6 3.6.6.6 0 1 .4 1 1V20c0 .6-.4 1-1 1A17 17 0 0 1 3 4c0-.6.4-1 1-1h3.5c.6 0 1 .4 1 1 0 1.3.2 2.5.6 3.6.1.3 0 .7-.2 1z" fill="#333"/></svg></span>
  <span>Call Us For Booking<br><em>555.201.4830</em></span>
</div>

<nav class="abs main-nav">
  <span>HOME</span><span>ABOUT US</span><span>SERVICES ⌄</span><span>GALLERY</span><span>TESTIMONIALS</span><span class="current">CONTACT US</span>
</nav>

<!-- hero -->
<div class="abs hero" role="img" aria-label="Photo of a mechanic's hand working in a car engine bay"></div>
<svg class="abs hero-tint" width="766" height="201" viewBox="0 0 766 201"><polygon points="0,0 392,0 272,201 0,201" fill="#8a0c12" opacity=".55"/></svg>
<div class="abs hero-eyebrow"><i></i>CONTACT</div>
<h1 class="abs hero-title cond">Contact Us Today!</h1>
<p class="abs hero-text">Quisque lorem neque, ultricies eget risus quis, fringilla interdum augue. Donec sollicitudin in ante sed consequat.</p>
<svg class="abs" style="left:0;top:279px" width="766" height="25" viewBox="0 0 766 25"><polygon points="212,0 766,0 766,19 688,19 603,1 240,24" fill="#ee0000"/></svg>

<!-- get in touch -->
<h2 class="abs touch-title cond">Have Questions? Get In Touch!</h2>
<p class="abs touch-sub cond">We're open for business 5 days a week. See<br>the <a href="#">opening hours</a> of our workshop</p>

<div class="abs info-card" style="left:72px">
  <div class="circle"><svg width="12" height="12" viewBox="0 0 24 24"><path d="M12 2a7 7 0 0 0-7 7c0 5 7 13 7 13s7-8 7-13a7 7 0 0 0-7-7zm0 9.5A2.5 2.5 0 1 1 12 6.5a2.5 2.5 0 0 1 0 5z" fill="#ee0000"/></svg></div>
  <h3 class="cond">Address</h3>
  <p>418 Harlow Bend Suite 3<br>Brookfield, TX 75990</p>
</div>
<div class="abs info-card dark" style="left:230px">
  <div class="circle"><svg width="12" height="12" viewBox="0 0 24 24"><path d="M6.6 10.8a15 15 0 0 0 6.6 6.6l2.2-2.2c.3-.3.7-.4 1-.2 1.1.4 2.3.6 3.6.6.6 0 1 .4 1 1V20c0 .6-.4 1-1 1A17 17 0 0 1 3 4c0-.6.4-1 1-1h3.5c.6 0 1 .4 1 1 0 1.3.2 2.5.6 3.6.1.3 0 .7-.2 1z" fill="#fff"/></svg></div>
  <h3 class="cond">Phone</h3>
  <p>Office: 555.201.4830<br>Cell: 555.274.9162</p>
</div>
<div class="abs info-card" style="left:388px">
  <div class="circle"><svg width="12" height="12" viewBox="0 0 24 24"><rect x="3" y="5" width="18" height="14" rx="2" fill="#ee0000"/><path d="M4 7l8 6 8-6" stroke="#fff" stroke-width="1.6" fill="none"/></svg></div>
  <h3 class="cond">Email</h3>
  <p>hello@corvanauto.com</p>
</div>
<div class="abs info-card" style="left:545px">
  <div class="circle"><svg width="12" height="12" viewBox="0 0 24 24"><circle cx="12" cy="12" r="10" fill="#ee0000"/><path d="M12 6v6l3 2" stroke="#fff" stroke-width="2" fill="none" stroke-linecap="round"/></svg></div>
  <h3 class="cond">Opening Hours</h3>
  <p>Monday to Friday<br>8:30-6pm</p>
</div>

<!-- message form -->
<div class="abs grey-band"></div>
<div class="abs form-panel"></div>
<div class="abs form-eyebrow cond"><i></i>GET AN APPOINTMENT</div>
<h2 class="abs form-title cond">Leave A Message</h2>
<p class="abs form-text">Lorem ipsum dolor sit amet, consectetur adipiscing elit, sed do eius tempor incididunt ut labore etdolore.</p>

<div class="abs field filled" style="left:95px;top:691px;width:151px;height:28px">Dana Reyes |<span class="fi"><svg width="7" height="7" viewBox="0 0 10 10"><circle cx="5" cy="3" r="2" fill="#333"/><path d="M1 10a4 4 0 0 1 8 0z" fill="#333"/></svg></span></div>
<div class="abs field" style="left:251px;top:691px;width:153px;height:28px">+ 00 555 200 1000<span class="fi"><svg width="7" height="7" viewBox="0 0 24 24"><path d="M6.6 10.8a15 15 0 0 0 6.6 6.6l2.2-2.2c.3-.3.7-.4 1-.2 1.1.4 2.3.6 3.6.6.6 0 1 .4 1 1V20c0 .6-.4 1-1 1A17 17 0 0 1 3 4c0-.6.4-1 1-1h3.5c.6 0 1 .4 1 1 0 1.3.2 2.5.6 3.6.1.3 0 .7-.2 1z" fill="#777"/></svg></span></div>
<div class="abs field" style="left:95px;top:723px;width:151px;height:28px">info@danareyes.com<span class="fi"><svg width="7" height="6" viewBox="0 0 10 8"><rect width="10" height="8" rx="1" fill="#777"/></svg></span></div>
<div class="abs field" style="left:251px;top:723px;width:153px;height:28px">Service<span class="fi"><svg width="6" height="4" viewBox="0 0 6 4"><path d="M0.5 0.5 3 3 5.5 0.5" stroke="#777" fill="none"/></svg></span></div>
<div class="abs field area" style="left:95px;top:756px;width:309px;height:67px">Message<span class="fi"><svg width="7" height="7" viewBox="0 0 10 10"><path d="M2 8 L3 5 L7 1 L9 3 L5 7 Z" fill="#777"/></svg></span></div>
<div class="abs submit cond"><svg width="9" height="9" viewBox="0 0 10 10"><path d="M10 0 L0 4 L4 6 L6 10 Z" fill="#fff"/></svg>SUBMIT</div>

<div class="abs map-box"><div class="map-fill" role="img" aria-label="Street map showing the shop location"></div></div>

<!-- footer -->
<footer class="abs site-footer"></footer>
<div class="abs footer-brand"><span class="brand-mark"></span><span>CORVAN AUTOMOTIVE</span></div>
<div class="abs badge" style="left:72px;top:1093px;width:59px;height:23px"></div>
<div class="abs badge" style="left:134px;top:1093px;width:49px;height:23px"></div>
<div class="abs badge" style="left:72px;top:1119px;width:32px;height:23px"></div>
<div class="abs badge" style="left:106px;top:1119px;width:59px;height:23px"></div>

<div class="abs footer-head cond" style="left:235px">Quick Links.</div>
<ul class="abs quick-links">
  <li>Home</li><li>About Us</li><li>Services</li><li>Gallery</li><li>Testimonials</li><li>Contact Us</li>
</ul>

<div class="abs footer-head cond" style="left:329px">Contact Us</div>
<div class="abs contact-row" style="top:1011px"><span class="ci"><svg width="9" height="9" viewBox="0 0 24 24"><path d="M12 2a7 7 0 0 0-7 7c0 5 7 13 7 13s7-8 7-13a7 7 0 0 0-7-7zm0 9.5A2.5 2.5 0 1 1 12 6.5a2.5 2.5 0 0 1 0 5z" fill="#555"/></svg></span><span>418 Harlow Bend Suite 3<br>Brookfield, TX 75990</span></div>
<div class="abs contact-row" style="top:1041px"><span class="ci"><svg width="9" height="9" viewBox="0 0 24 24"><path d="M6.6 10.8a15 15 0 0 0 6.6 6.6l2.2-2.2c.3-.3.7-.4 1-.2 1.1.4 2.3.6 3.6.6.6 0 1 .4 1 1V20c0 .6-.4 1-1 1A17 17 0 0 1 3 4c0-.6.4-1 1-1h3.5c.6 0 1 .4 1 1 0 1.3.2 2.5.6 3.6.1.3 0 .7-.2 1z" fill="#555"/></svg></span><span><b>OFFICE:</b> 555.201.4830<br><b>Phone:</b> 555.274.9162</span></div>
<div class="abs contact-row" style="top:1073px"><span class="ci"><svg width="9" height="9" viewBox="0 0 24 24"><rect x="3" y="5" width="18" height="14" rx="2" fill="#555"/><path d="M4 7l8 6 8-6" stroke="#d5d5d5" stroke-width="1.6" fill="none"/></svg></span><span>hello@corvanauto.com</span></div>
<div class="abs contact-row" style="top:1103px"><span class="ci"><svg width="9" height="9" viewBox="0 0 24 24"><circle cx="12" cy="12" r="10" fill="#555"/><path d="M12 6v6l3 2" stroke="#d5d5d5" stroke-width="2" fill="none"/></svg></span><span><b>Hours of Operation:</b> M-F 8:30-6pm</span></div>

<div class="abs footer-map" role="img" aria-label="Area map of the neighbourhood around the shop"></div>

<svg class="abs" style="left:0;top:1172px" width="766" height="28" viewBox="0 0 766 28"><polygon points="0,26 200,26 200,28 0,28" fill="#ee0000"/><polygon points="212,28 228,0 766,0 766,28" fill="#ee0000"/><polygon points="202,28 218,0 222,0 206,28" fill="#888"/></svg>
<div class="abs social" style="left:97px"></div>
<div class="abs social" style="left:118px"></div>
<div class="abs social" style="left:140px"></div>
<div class="abs copyright">Copyright © 2024 Corvan Automotive LLC. All Rights Reserved.</div>

</body>
</html>
```